We want to design total new business card and logo for Kestrel Building Services Ltd

Our company name Kestrel Building Services Ltd. Design new logo and business card , need hi-end luxury style art for architecture and construction industry. The card should simple but stylish. Our business focus on CONNECT tradesman to construction company, help marketing construction company tender oversea projects, managing franchise in construction sector, delivery amazing services to our client, so Logo should show the CONNECTION IDEA, CONNECTING PEOPLE, LUXURY. Visit our website for more information: kestrelgroup.example.nz

Target Market(s)

Directors or managers

Industry/Entity Type

Construction Company

Contact Information for Business Card

Name, Title, Mobile, Email, Website

Font styles to use
Serif

Colors

Designer to choose colors to be used in the design.

Requirements
Must have
• Simple and luxury, connection icon
Nice to have
• Special materials, plastic card, look through,...
• Look new ideas.

```html
<!DOCTYPE html>
<html lang="en">
<head>
<meta charset="utf-8">
<title>Kestrel Building Services Ltd — Business Card</title>
<link href="https://fonts.googleapis.com/css2?family=Lora:wght@400;500&display=swap" rel="stylesheet">
<style>
  :root {
    --backdrop: #1c1c1c;
    --card: #262626;
    --card-edge: #2e2e2e;
    --silver: #c9c9c9;
    --white: #f2f2f2;
    --accent: #1f5fc0;
  }
  html, body {
    margin: 0;
    padding: 0;
    width: 1200px;
    height: 900px;
    overflow: hidden;
    background: var(--backdrop);
    font-family: "Lora", serif;
  }
  .canvas {
    position: relative;
    width: 1200px;
    height: 900px;
  }
  .card {
    position: absolute;
    left: 250px;
    width: 700px;
    height: 400px;
    background: linear-gradient(135deg, var(--card) 0%, var(--card-edge) 100%);
    box-shadow: 0 12px 30px rgba(0,0,0,0.55);
    box-sizing: border-box;
  }
  .card--front { top: 35px; }
  .card--back  { top: 465px; }

  /* Front */
  .brand {
    position: absolute;
    inset: 0;
    display: flex;
    flex-direction: column;
    align-items: center;
    justify-content: center;
    gap: 22px;
  }
  .brand__dot {
    width: 54px;
    height: 54px;
    border-radius: 50%;
    background: var(--silver);
  }
  .brand__name {
    margin: 0;
    color: var(--silver);
    font-weight: 500;
    font-size: 26px;
    letter-spacing: 3px;
    text-transform: uppercase;
    text-align: center;
    line-height: 1.3;
  }

  /* Back */
  .identity {
    position: absolute;
    right: 380px;
    top: 160px;
    text-align: right;
  }
  .identity__name {
    margin: 0 0 6px;
    color: var(--accent);
    font-weight: 500;
    font-size: 26px;
    line-height: 1.2;
    text-transform: uppercase;
  }
  .identity__title {
    margin: 0;
    color: var(--white);
    font-size: 18px;
    letter-spacing: 1px;
    line-height: 1.4;
  }
  .divider {
    position: absolute;
    left: 345px;
    top: 155px;
    width: 2px;
    height: 88px;
    background: var(--accent);
  }
  .contacts {
    position: absolute;
    left: 372px;
    top: 160px;
    margin: 0;
    padding: 0;
    list-style: none;
  }
  .contacts__item {
    display: flex;
    align-items: center;
    gap: 12px;
    color: var(--white);
    font-size: 17px;
    letter-spacing: 0.5px;
    line-height: 26px;
  }
  .contacts__icon {
    width: 14px;
    height: 14px;
    flex: none;
  }
</style>
</head>
<body>
<main class="canvas">
  <section class="card card--front" aria-label="Card front">
    <div class="brand">
      <span class="brand__dot" aria-hidden="true"></span>
      <p class="brand__name">Kestrel Building<br>Services Ltd</p>
    </div>
  </section>

  <section class="card card--back" aria-label="Card back">
    <div class="identity">
      <h1 class="identity__name">Daniel Hartley</h1>
      <p class="identity__title">Director</p>
    </div>
    <div class="divider" aria-hidden="true"></div>
    <ul class="contacts">
      <li class="contacts__item">
        <svg class="contacts__icon" viewBox="0 0 16 16" aria-hidden="true"><path d="M4 1l2 4-1.5 1.5a9 9 0 0 0 5 5L11 10l4 2-1 3c-7 0-13-6-13-13z" fill="var(--accent)"/></svg>
        +330 2460-5512
      </li>
      <li class="contacts__item">
        <svg class="contacts__icon" viewBox="0 0 16 16" aria-hidden="true"><rect x="1.5" y="3.5" width="13" height="9" fill="none" stroke="var(--accent)" stroke-width="1.4"/><path d="M1.5 3.5L8 9l6.5-5.5" fill="none" stroke="var(--accent)" stroke-width="1.4"/></svg>
        info@kestrelbuilding.example
      </li>
      <li class="contacts__item">
        <svg class="contacts__icon" viewBox="0 0 16 16" aria-hidden="true"><circle cx="8" cy="8" r="6.5" fill="none" stroke="var(--accent)" stroke-width="1.3"/><ellipse cx="8" cy="8" rx="3" ry="6.5" fill="none" stroke="var(--accent)" stroke-width="1.1"/><path d="M1.5 8h13" stroke="var(--accent)" stroke-width="1.1"/></svg>
        www.kestrelbuilding.example
      </li>
    </ul>
  </section>
</main>
</body>
</html>
```